Ferncliff Capital - Website Design

We need a website design for a new commercial real estate company called Ferncliff Capital. We're effectively commercial mortgage brokers connecting real estate investors to lenders. We need a website that is simple (not busy), elegant, professional, and user-friendly. A lot of the users will be in their 50's and less tech savvy, so a stream-lined design is best. The website will serve as a portal for lenders to review new financing opportunities, as well as for real estate investors to review terms from lenders.
Updates
Just uploaded our logo.
Target Market(s)
Commercial real estate investors and lenders
Industry/Entity Type
Real Estate
Number of Pages Required
1 page
Colors
Designer to choose colors to be used in the design.
Look and feel

```html
<!DOCTYPE html>
<html lang="en">
<head>
<meta charset="utf-8">
<title>Ferncliff Capital</title>
<link href="https://fonts.googleapis.com/css2?family=Lato:wght@400;700;900&family=Open+Sans:wght@400;600;700&display=swap" rel="stylesheet">
<style>
:root{
  --navy:#1c4c92;
  --navy-deep:#173f7a;
  --green:#6e9a10;
  --green-dark:#5c820a;
  --ink:#333b47;
  --muted:#7b828c;
  --line:#e3e6ea;
  --white:#ffffff;
}
*{box-sizing:border-box;margin:0;padding:0}
html,body{width:1200px;height:3586px;overflow:hidden}
body{position:relative;background:var(--white);font-family:"Open Sans",Arial,sans-serif;color:var(--ink)}
.abs{position:absolute}
h1,h2,h3,.heading{font-family:"Lato",Arial,sans-serif}

/* header */
.site-header{left:0;top:0;width:1200px;height:105px;background:var(--white);border-top:4px solid var(--green);z-index:3}
.brand{left:98px;top:28px;line-height:1}
.brand-name{font-family:"Lato",sans-serif;font-weight:900;font-size:27px;color:var(--navy);letter-spacing:.5px}
.brand-tag{display:block;text-align:right;font-family:"Lato",sans-serif;font-size:15px;color:var(--green);margin-top:2px}
.main-nav{right:98px;top:44px;display:flex;gap:30px;align-items:center}
.main-nav a{font-family:"Open Sans",sans-serif;font-weight:700;font-size:13.5px;color:#2b3340;text-decoration:none;text-transform:uppercase}
.main-nav a.active{color:var(--green)}

/* hero */
.hero{left:0;top:105px;width:1200px;height:620px;background:linear-gradient(120deg,#cfd6dd 0%,#eef0f2 35%,#bfc7cf 70%,#8f9aa6 100%)}
.hero-title{left:96px;top:340px;font-weight:900;font-size:58px;line-height:66px;color:var(--white);letter-spacing:1px;text-shadow:0 2px 6px rgba(0,0,0,.25)}
.slide-arrow{width:36px;height:36px;border-radius:50%;background:rgba(60,60,60,.55)}
.slide-arrow svg{display:block;margin:11px auto}
.hero-curve{left:0;top:610px}

.quote-box{left:722px;top:418px;width:378px;height:402px;background:var(--navy);z-index:2;padding:30px 32px 0;color:var(--white)}
.quote-box h2{font-size:29px;font-weight:900;text-align:center;letter-spacing:.5px}
.quote-box .sub{font-size:12.5px;text-align:center;margin-top:10px}
.quote-fields{display:grid;grid-template-columns:1fr 1fr;gap:12px 12px;margin-top:24px}
.field{height:36px;background:var(--white);border-radius:2px;font-size:11.5px;color:#777;padding:11px 10px}
.field.wide{grid-column:1/3}
.purpose{display:flex;align-items:center;font-size:12px;margin-top:20px;padding-left:12px}
.purpose .opt{display:flex;align-items:center;gap:6px;margin-left:24px}
.purpose .opt:first-of-type{margin-left:auto;margin-right:0}
.dot{width:11px;height:11px;border-radius:50%;background:var(--white)}
.btn{display:inline-block;background:var(--green);color:var(--white);font-family:"Open Sans",sans-serif;font-weight:700;font-size:14px;text-transform:uppercase;border-radius:22px;text-align:center}
.quote-box .btn{display:block;width:152px;height:38px;line-height:38px;margin:20px auto 0}

/* mortgage */
.media-frame{left:67px;top:868px;width:428px;height:300px;border:3px solid var(--green)}
.media{left:98px;top:903px;width:464px;height:311px;background:linear-gradient(135deg,#1c6fb0 0%,#3aa0d8 40%,#5fb85a 75%,#2b7a3c 100%)}
.play{left:306px;top:1035px;width:52px;height:52px;border-radius:50%;background:#d02a2a}
.section-title{font-weight:900;color:var(--navy);font-size:32px;letter-spacing:.5px}
.mortgage-title{left:620px;top:898px}
.copy{font-size:13.5px;line-height:24px;color:var(--muted)}
.mortgage-copy{left:620px;top:962px;width:482px}
.mortgage-copy p+p{margin-top:22px}
.btn-outline{left:620px;top:1172px;width:136px;height:42px;border:1px solid #cfd3d8;border-radius:22px;font-size:12.5px;font-weight:700;color:#444;text-transform:uppercase;display:flex;align-items:center;justify-content:center;gap:6px}

/* consultation */
.consult{left:0;top:1303px;width:1200px;height:389px;background:linear-gradient(180deg,#3b3f45 0%,#4a4640 55%,#5c5145 100%)}
.consult-title{left:0;width:1200px;top:1388px;text-align:center;color:var(--white);font-weight:900;font-size:32px;letter-spacing:.5px}
.consult-copy{left:230px;width:740px;top:1452px;text-align:center;color:#e9ecef;font-size:14px;line-height:25px}
.consult .btn{}
.consult-btn{left:510px;top:1545px;width:180px;height:50px;line-height:50px}

/* services */
.services-title{left:0;width:1200px;top:1766px;text-align:center}
.services-sub{left:330px;width:540px;top:1834px;text-align:center;font-size:13px;line-height:24px;color:var(--muted)}
.service{width:360px;text-align:center}
.service-icon{width:134px;height:134px;border-radius:50%;background:var(--green);margin:0 auto;border:6px solid #fff;box-shadow:0 0 0 2px var(--green);display:flex;align-items:center;justify-content:center}
.service h3{font-family:"Open Sans",sans-serif;font-size:16px;font-weight:600;text-transform:uppercase;color:#2b3340;margin-top:32px}
.service p{font-size:12.5px;line-height:23px;color:var(--muted);width:300px;margin:14px auto 0}

/* testimonials */
.testimonials{left:0;top:2247px;width:1200px;height:466px;background:linear-gradient(100deg,#5a6673 0%,#8c97a2 45%,#6b7480 75%,#3e4753 100%)}
.testimonials-title{left:0;width:1200px;top:2318px;text-align:center;color:var(--white);font-weight:900;font-size:32px}
.avatar{left:533px;top:2405px;width:134px;height:134px;border-radius:50%;background:linear-gradient(160deg,#d9c2b0,#9a6b52);border:5px solid #fff}
.quote-text{left:300px;width:600px;top:2568px;text-align:center;color:var(--white);font-size:15px;line-height:28px}
.quote-author{left:0;width:1200px;top:2644px;text-align:center;color:var(--white);font-size:13px}
.quote-author b{font-weight:700}
.quote-mark{font-family:"Lato",sans-serif;font-weight:900;font-size:110px;color:rgba(255,255,255,.35);line-height:1}

/* clients */
.clients-title{left:0;width:1200px;top:2792px;text-align:center}
.clients-sub{left:0;width:1200px;top:2854px;text-align:center;font-size:13px;color:var(--muted)}
.client-row{left:98px;top:2910px;display:flex;gap:19px}
.client{width:186px;height:108px;background:#fff;border:1px solid var(--line);border-bottom:4px solid var(--green);box-shadow:0 2px 6px rgba(0,0,0,.06);display:flex;align-items:center;justify-content:center;gap:8px;font-family:"Open Sans",sans-serif;font-weight:700;font-size:19px;color:#6a7079}
.client i{width:14px;height:14px;border-radius:50%;background:#6a7079;display:block}
.pager{left:573px;top:3062px;display:flex;gap:8px}
.pager span{width:11px;height:11px;border-radius:50%;border:1px solid #b9bec4}
.pager span.on{background:var(--green);border-color:var(--green)}

/* footer */
.site-footer{left:0;top:3107px;width:1200px;height:479px;background:var(--navy-deep);color:var(--white)}
.footer-top{left:0;top:0}
.foot-col{top:150px}
.foot-col h4{font-family:"Open Sans",sans-serif;font-weight:700;font-size:15px;text-transform:uppercase;letter-spacing:.3px}
.contact-list{margin-top:38px;list-style:none;font-size:12.5px;line-height:20px}
.contact-list li{display:flex;gap:16px;margin-bottom:20px}
.contact-list svg{flex:none;margin-top:2px}
.link-list{list-style:none;margin-top:40px;font-size:12.5px}
.link-list li{margin-bottom:13px;display:flex;align-items:center;gap:12px}
.newsletter p{font-size:12.5px;line-height:20px;margin-top:40px;width:280px}
.news-input{width:278px;height:40px;border:1px solid rgba(255,255,255,.7);margin-top:12px;font-size:12px;padding:12px 10px}
.site-footer .btn{width:112px;height:36px;line-height:36px;font-size:12.5px;margin-top:14px}
.foot-rule{left:98px;top:413px;width:1004px;height:1px;background:rgba(255,255,255,.35)}
.copyright{left:98px;top:427px;font-size:12px}
.social{right:100px;top:420px;display:flex;gap:12px}
.social span{width:34px;height:34px;border-radius:50%;border:2px solid rgba(255,255,255,.85)}
</style>
</head>
<body>

<header class="site-header abs">
  <div class="brand abs"><span class="brand-name">FERNCLIFF</span><span class="brand-tag">Capital</span></div>
  <nav class="main-nav abs">
    <a class="active">Home</a><a>About Us</a><a>Loans</a><a>Services</a><a>Blog</a><a>Contact Us</a>
    <svg width="14" height="14" viewBox="0 0 14 14"><circle cx="6" cy="6" r="4.5" fill="none" stroke="#2b3340" stroke-width="2"/><line x1="9.3" y1="9.3" x2="13" y2="13" stroke="#2b3340" stroke-width="2"/></svg>
  </nav>
</header>

<section class="hero abs" role="img" aria-label="Photo of three smiling colleagues working together at an office desk"></section>
<h1 class="hero-title abs">FERNCLIFF<br>CAPITAL</h1>
<div class="slide-arrow abs" style="left:22px;top:390px"><svg width="12" height="14" viewBox="0 0 12 14"><path d="M8 2 3 7l5 5" fill="none" stroke="#fff" stroke-width="2"/></svg></div>
<div class="slide-arrow abs" style="left:1142px;top:390px"><svg width="12" height="14" viewBox="0 0 12 14"><path d="M4 2l5 5-5 5" fill="none" stroke="#fff" stroke-width="2"/></svg></div>
<svg class="hero-curve abs" width="1200" height="120" viewBox="0 0 1200 120">
  <path d="M0 0 C300 120 700 80 1200 10 L1200 120 L0 120Z" fill="#fff"/>
  <path d="M0 5 C300 118 700 78 1200 8" fill="none" stroke="var(--navy)" stroke-width="4"/>
</svg>

<form class="quote-box abs">
  <h2>GET A QUICK QUOTE</h2>
  <p class="sub">We are a new commercial real estate company.</p>
  <div class="quote-fields">
    <div class="field">First Name</div><div class="field">Last Name</div>
    <div class="field">Phone</div><div class="field">Postcode</div>
    <div class="field wide">Email Address</div>
  </div>
  <div class="purpose">Finance For Loan Purpose
    <span class="opt"><span class="dot"></span>No</span>
    <span class="opt"><span class="dot"></span>Yes</span>
  </div>
  <span class="btn">Get a Quote</span>
</form>

<div class="media-frame abs"></div>
<div class="media abs" role="img" aria-label="Illustration of city buildings over a world map with rising growth arrows"></div>
<div class="play abs"><svg width="52" height="52" viewBox="0 0 52 52"><path d="M21 16l15 10-15 10z" fill="#fff"/></svg></div>
<h2 class="section-title mortgage-title abs">MORTGAGE BROKERS</h2>
<div class="copy mortgage-copy abs">
  <p>We connect commercial property investors with trusted lenders, offering clear terms and a simple path from enquiry to funding.</p>
  <p>Our brokers review every opportunity in detail, match it to the right lending partners and guide you through each step. Lenders can browse new financing requests while investors compare terms side by side, all in one calm and easy portal.</p>
</div>
<div class="btn-outline abs">Read More <svg width="12" height="12" viewBox="0 0 12 12"><circle cx="6" cy="6" r="6" fill="#444"/><path d="M5 3.5 7.5 6 5 8.5" fill="none" stroke="#fff" stroke-width="1.5"/></svg></div>

<section class="consult abs" role="img" aria-label="Photo of a modern commercial retail building frontage"></section>
<h2 class="consult-title abs">GET FREE CONSULTATION</h2>
<p class="consult-copy abs">Speak with one of our experienced brokers about your next purchase or refinance and get a clear view of the options open to you today.</p>
<span class="btn consult-btn abs">Get Started</span>

<h2 class="section-title services-title abs">OUR SERVICES</h2>
<p class="services-sub abs">From first enquiry to completion, we make commercial property finance clear, fair and easy to follow.</p>
<div class="service abs" style="left:60px;top:1918px">
  <div class="service-icon"><svg width="56" height="56" viewBox="0 0 56 56"><rect x="12" y="10" width="32" height="38" fill="none" stroke="#fff" stroke-width="4"/><rect x="19" y="18" width="6" height="6" fill="#fff"/><rect x="31" y="18" width="6" height="6" fill="#fff"/><rect x="19" y="29" width="6" height="6" fill="#fff"/><rect x="31" y="29" width="6" height="6" fill="#fff"/><rect x="24" y="39" width="8" height="9" fill="#fff"/></svg></div>
  <h3>Commercial Mortgages</h3>
  <p>Tailored loans for offices, retail units and mixed use buildings.</p>
</div>
<div class="service abs" style="left:420px;top:1918px">
  <div class="service-icon"><svg width="56" height="56" viewBox="0 0 56 56"><rect x="9" y="15" width="38" height="26" rx="3" fill="none" stroke="#fff" stroke-width="4"/><line x1="9" y1="24" x2="47" y2="24" stroke="#fff" stroke-width="4"/><line x1="10" y1="46" x2="46" y2="10" stroke="#fff" stroke-width="4"/></svg></div>
  <h3>Bad Credit Finance</h3>
  <p>Flexible options for borrowers with a less than perfect record.</p>
</div>
<div class="service abs" style="left:775px;top:1918px">
  <div class="service-icon"><svg width="56" height="56" viewBox="0 0 56 56"><path d="M8 28 26 12l18 16" fill="none" stroke="#fff" stroke-width="4"/><path d="M14 24v20h14" fill="none" stroke="#fff" stroke-width="4"/><circle cx="36" cy="36" r="7" fill="none" stroke="#fff" stroke-width="4"/><line x1="41" y1="41" x2="48" y2="48" stroke="#fff" stroke-width="4"/></svg></div>
  <h3>Finance for HMO Properties</h3>
  <p>Funding for houses in multiple occupation across the region.</p>
</div>

<section class="testimonials abs" role="img" aria-label="Photo of two business people shaking hands"></section>
<h2 class="testimonials-title abs">WHAT OUR CLIENTS SAY</h2>
<span class="quote-mark abs" style="left:96px;top:2355px">&ldquo;</span>
<span class="quote-mark abs" style="left:1060px;top:2580px">&rdquo;</span>
<div class="slide-arrow abs" style="left:22px;top:2462px"><svg width="12" height="14" viewBox="0 0 12 14"><path d="M8 2 3 7l5 5" fill="none" stroke="#fff" stroke-width="2"/></svg></div>
<div class="slide-arrow abs" style="left:1142px;top:2462px"><svg width="12" height="14" viewBox="0 0 12 14"><path d="M4 2l5 5-5 5" fill="none" stroke="#fff" stroke-width="2"/></svg></div>
<div class="avatar abs" role="img" aria-label="Portrait of the client"></div>
<p class="quote-text abs">&ldquo; Lorem Ipsum is simply dummy text of the printing and typesetting industry.<br>Lorem Ipsum has been the industry's standard dummy text ever. &rdquo;</p>
<p class="quote-author abs"><b>DANA WHITFIELD</b>, Creative Manager</p>

<h2 class="section-title clients-title abs">OUR CLIENTS LIST</h2>
<p class="clients-sub abs">Some of the investors and lenders who trust us with their commercial property finance.</p>
<div class="client-row abs">
  <div class="client"><i></i>Tideline</div>
  <div class="client">Northvane</div>
  <div class="client">Halvorsen</div>
  <div class="client">Brightwell</div>
  <div class="client">Quillon</div>
</div>
<div class="pager abs"><span></span><span class="on"></span><span></span></div>

<footer class="site-footer abs">
  <svg class="footer-top abs" width="1200" height="100" viewBox="0 0 1200 100">
    <polygon points="0,0 1200,0 1200,12 600,96 0,12" fill="var(--green)"/>
    <polygon points="0,0 1200,0 600,82" fill="#fff"/>
  </svg>
  <div class="foot-col abs" style="left:100px">
    <h4>Contact Us</h4>
    <ul class="contact-list">
      <li><svg width="14" height="18" viewBox="0 0 14 18"><path d="M7 17S1 10 1 6.5a6 6 0 0 1 12 0C13 10 7 17 7 17z" fill="none" stroke="#fff" stroke-width="1.6"/><circle cx="7" cy="6.5" r="2" fill="#fff"/></svg><span>Harbour Lane, Westmoor,<br>North County</span></li>
      <li><svg width="14" height="14" viewBox="0 0 14 14"><path d="M3 1l2.5 3-1.5 1.5a8 8 0 0 0 4.5 4.5L10 8.5l3 2.5-1.5 2.5C6 13 1 8 .5 2.5z" fill="#fff"/></svg><span>(+1) 555 014 2290</span></li>
      <li><svg width="15" height="12" viewBox="0 0 15 12"><rect x="1" y="1" width="13" height="10" fill="none" stroke="#fff" stroke-width="1.5"/><path d="M1 1l6.5 5.5L14 1" fill="none" stroke="#fff" stroke-width="1.5"/></svg><span><b>info@ferncliffcapital.com</b></span></li>
    </ul>
  </div>
  <div class="foot-col abs" style="left:383px">
    <h4>Quick Links</h4>
    <ul class="link-list"><li>&rsaquo; Home</li><li>&rsaquo; About Us</li><li>&rsaquo; Loans</li><li>&rsaquo; Finance</li></ul>
  </div>
  <div class="foot-col abs" style="left:595px">
    <h4>Other Links</h4>
    <ul class="link-list"><li>&rsaquo; Contact us</li><li>&rsaquo; Book A Callback</li><li>&rsaquo; FAQs</li><li>&rsaquo; Terms &amp; Conditions</li></ul>
  </div>
  <div class="foot-col newsletter abs" style="left:825px">
    <h4>Join Our Newsletter</h4>
    <p>Register your Email Address to get information about us</p>
    <div class="news-input">Email Address</div>
    <span class="btn">Subscribe</span>
  </div>
  <div class="foot-rule abs"></div>
  <p class="copyright abs">&copy; Copyright 2017 Ferncliff Capital. All Rights Reserved</p>
  <div class="social abs"><span></span><span></span><span></span><span></span></div>
</footer>

</body>
</html>
```